Window and GutterCleaning Flyer A5 size double sided.

We need a double sided A5 flyer. Side 1, is for window cleaning, side 2 is for gutter cleaning. Licensed by Borough of Marlow Council.
Phone number 0800 473 1926.
Business address 17 Fallowmere Close, North Brack Edinburgh EH31 4LP.
www.clearpane-hub-services.com
We use a LoftEye Gutter inspection Cam to view your gutters first to see if they need doing.
Window cleaning ; Professional window cleaning services, what we offer, water fed pole window cleaning able to reach windows up to 60 feet.
Conservatory cleaning.
Conservatory roof cleaning.
Fascias & Soffits cleaning.
Excellent Customer Service.
Target Market(s)
domestic houses
Industry/Entity Type
window cleaning
Look and feel
Each slider illustrates characteristics of the customer's brand and the style your logo design should communicate.

```html
<!DOCTYPE html>
<html lang="en">
<head>
<meta charset="utf-8">
<title>ClearPane Hub – Window and Gutter Cleaning Flyer</title>
<link href="https://fonts.googleapis.com/css2?family=Montserrat:ital,wght@0,400;0,500;0,600;0,700;0,800;0,900;1,700&display=swap" rel="stylesheet">
<style>
:root{
  --bg:#d9d9d9;
  --navy:#27235e;
  --navy-deep:#1f1b52;
  --sky:#8fb4e8;
  --yellow:#f5c21a;
  --red:#e3151b;
  --green:#3b7d24;
  --white:#ffffff;
  --panel:#e3e4ea;
}
*{box-sizing:border-box;margin:0;padding:0}
html,body{width:1200px;height:1049px;overflow:hidden;background:var(--bg);font-family:"Montserrat",sans-serif}
.canvas{position:relative;width:1200px;height:1049px}
.flyer{position:absolute;top:155px;width:477px;height:675px;background:var(--white);overflow:hidden;color:var(--navy)}
.flyer--windows{left:106px}
.flyer--gutters{left:642px}
.flyer-art{position:absolute;inset:0}
.abs{position:absolute;white-space:nowrap}
.wrap{white-space:normal}
.brand{position:absolute;left:40px;top:44px;display:flex;align-items:center;gap:6px}
.brand-mark{width:14px;height:14px;background:var(--navy)}
.brand-name{font-weight:800;font-size:15px;color:var(--navy);line-height:1}
.kicker{font-weight:500;color:var(--white);letter-spacing:1px;line-height:1}
.headline-line{font-weight:900;line-height:1;letter-spacing:.5px}
.sky{color:var(--sky)}
.yellow{color:var(--yellow)}
.white{color:var(--white)}
.red{color:var(--red)}
.body-copy{font-size:8.6px;line-height:1.3;color:var(--white);font-weight:500}
.section-title{font-weight:900;color:var(--navy);text-align:center;line-height:1}
.pill{position:absolute;width:164px;height:35px;border-radius:18px;background:var(--navy);display:flex;align-items:center;color:var(--white);font-size:8.6px;line-height:1.2}
.pill-icon{width:35px;height:35px;border-radius:50%;background:var(--sky);margin-right:6px;flex:none;display:flex;align-items:center;justify-content:center}
.tagline{font-weight:800;font-size:20px;text-align:center;width:477px;color:var(--navy);line-height:1}
.subline{font-weight:700;font-style:italic;font-size:10.5px;text-align:center;width:477px;color:var(--navy-deep);line-height:1}
.footer-title{font-weight:700;font-size:11px;line-height:1.05;text-transform:uppercase}
.contact{font-size:10px;color:var(--white);display:flex;align-items:flex-start;gap:5px;line-height:1.2;font-weight:500}
.contact svg{flex:none;margin-top:2px}
.arrow-label{position:absolute;height:30px;color:var(--white);font-weight:700;font-size:14px;display:flex;align-items:center;padding-left:14px}
.small-bold{font-weight:700;font-size:11px;line-height:1.15}
.tile{position:absolute;top:462px;width:60px;height:71px;background:var(--navy);border-radius:3px;overflow:hidden}
.tile-photo{height:48px}
.tile-caption{font-size:5.2px;font-weight:700;color:var(--white);text-align:center;line-height:1.15;padding-top:4px}
.why{position:absolute;left:300px;top:362px;width:150px;height:198px;background:var(--panel);border-radius:4px}
.why-head{position:absolute;left:-10px;top:14px;width:152px;height:26px;background:var(--navy);border-radius:0 6px 6px 0;color:var(--white);font-size:12.5px;font-weight:500;display:flex;align-items:center;justify-content:center}
.why-item{position:absolute;left:6px;width:136px;display:flex;align-items:center;gap:8px;font-size:8.4px;font-weight:600;line-height:1.2;color:var(--navy-deep);border-bottom:1px solid #c6c7d2;padding-bottom:5px}
.why-icon{width:22px;height:22px;border-radius:50%;background:var(--navy);flex:none;display:flex;align-items:center;justify-content:center}
</style>
</head>
<body>
<main class="canvas">

<!-- SIDE 1: WINDOWS -->
<section class="flyer flyer--windows">
  <svg class="flyer-art" width="477" height="675" viewBox="0 0 477 675">
    <defs>
      <linearGradient id="w-top" x1="0" y1="0" x2="1" y2="1"><stop offset="0" stop-color="#8a6f5c"/><stop offset=".5" stop-color="#b9a48c"/><stop offset="1" stop-color="#6a4a3a"/></linearGradient>
      <linearGradient id="w-c1" x1="0" y1="0" x2="1" y2="1"><stop offset="0" stop-color="#c8ccd2"/><stop offset="1" stop-color="#7d8894"/></linearGradient>
      <linearGradient id="w-c2" x1="0" y1="0" x2="0" y2="1"><stop offset="0" stop-color="#a9c7e8"/><stop offset="1" stop-color="#a5603f"/></linearGradient>
    </defs>
    <path d="M208 0 H477 V160 H215 C180 110 180 40 208 0 Z" fill="var(--sky)"/>
    <path d="M218 0 H477 V160 H225 C195 110 195 40 218 0 Z" fill="url(#w-top)" role="img" aria-label="Cleaner in a hi-vis vest using a water-fed pole on a conservatory"/>
    <path d="M0 318 C90 322 190 345 282 366 C180 362 80 364 0 372 Z" fill="var(--sky)"/>
    <path d="M0 137 C110 118 230 120 330 134 C410 146 450 138 477 128 V322 C420 345 340 368 270 362 C180 352 90 328 0 333 Z" fill="var(--navy)"/>
    <circle cx="384" cy="229" r="77" fill="var(--white)"/>
    <circle cx="384" cy="229" r="73" fill="url(#w-c1)" role="img" aria-label="Pole brush cleaning a window pane"/>
    <circle cx="353" cy="303" r="56" fill="var(--white)"/>
    <circle cx="353" cy="303" r="52" fill="url(#w-c2)" role="img" aria-label="White conservatory with a glass roof"/>
    <line x1="24" y1="267" x2="272" y2="267" stroke="var(--white)" stroke-width=".7"/>
    <path d="M0 573 C150 562 330 556 477 558 V600 H0 Z" fill="var(--sky)"/>
    <path d="M0 586 C150 574 330 566 477 569 V675 H0 Z" fill="var(--navy)"/>
  </svg>

  <div class="brand"><span class="brand-mark"></span><span class="brand-name">ClearPane Hub</span></div>

  <p class="abs kicker" style="left:24px;top:160px;font-size:13.5px">LET THE SUNSHINE IN</p>
  <h1>
    <span class="abs headline-line sky" style="left:23px;top:177px;font-size:34px">SPARKLING</span>
    <span class="abs headline-line sky" style="left:23px;top:207px;font-size:34px">WINDOWS</span>
    <span class="abs headline-line yellow" style="left:24px;top:239px;font-size:23px">GUARANTEED</span>
  </h1>
  <p class="abs body-copy wrap" style="left:24px;top:276px;width:250px">We offer high-quality window cleaning for domestic homes, delivering spotless, streak-free results every time. Water-fed pole cleaning reaching windows up to 60 feet.</p>

  <h2 class="abs section-title" style="left:0;width:477px;top:370px;font-size:22px">WE OFFER</h2>

  <div class="pill" style="left:34px;top:402px"><span class="pill-icon"><svg width="16" height="16" viewBox="0 0 16 16"><rect x="3" y="2" width="10" height="12" fill="none" stroke="var(--navy)" stroke-width="1.4"/><line x1="8" y1="2" x2="8" y2="14" stroke="var(--navy)" stroke-width="1.2"/></svg></span>Water-Fed Pole Cleaning<br>– Up to 60 Feet</div>
  <div class="pill" style="left:34px;top:443px"><span class="pill-icon"><svg width="16" height="16" viewBox="0 0 16 16"><path d="M1 12 L8 4 L15 12" fill="none" stroke="var(--navy)" stroke-width="1.6"/></svg></span>Fascia &amp; Soffit Cleaning</div>
  <div class="pill" style="left:34px;top:484px"><span class="pill-icon"><svg width="16" height="16" viewBox="0 0 16 16"><path d="M3 8 L7 12 L13 4" fill="none" stroke="var(--navy)" stroke-width="1.8"/></svg></span>Reliable, Friendly Service</div>
  <div class="pill" style="left:258px;top:402px"><span class="pill-icon"><svg width="16" height="16" viewBox="0 0 16 16"><path d="M2 7 L8 2 L14 7 V14 H2 Z" fill="none" stroke="var(--navy)" stroke-width="1.4"/></svg></span>Conservatory Windows<br>&amp; Roofs</div>
  <div class="pill" style="left:258px;top:443px"><span class="pill-icon"><svg width="16" height="16" viewBox="0 0 16 16"><circle cx="8" cy="8" r="6" fill="none" stroke="var(--navy)" stroke-width="1.4"/><path d="M8 4 V8 L11 10" fill="none" stroke="var(--navy)" stroke-width="1.4"/></svg></span>One-off or<br>Regular Cleans</div>
  <div class="pill" style="left:258px;top:484px"><span class="pill-icon"><svg width="16" height="16" viewBox="0 0 16 16"><rect x="3" y="2" width="10" height="12" fill="none" stroke="var(--navy)" stroke-width="1.4"/><line x1="5" y1="6" x2="11" y2="6" stroke="var(--navy)"/><line x1="5" y1="9" x2="11" y2="9" stroke="var(--navy)"/></svg></span>Licensed by<br>Borough of Marlow Council</div>

  <p class="abs tagline" style="left:0;top:530px">Great service from start to finish</p>
  <p class="abs subline" style="left:0;top:553px">Reliable, professional and the windows have never looked better!</p>

  <p class="abs footer-title red" style="left:40px;top:612px;font-size:12.5px">Get free quote today!</p>
  <div class="abs contact" style="left:40px;top:632px"><svg width="8" height="8" viewBox="0 0 8 8"><circle cx="4" cy="4" r="4" fill="var(--sky)"/></svg>0800 473 1926</div>
  <div class="abs contact" style="left:40px;top:646px"><svg width="8" height="8" viewBox="0 0 8 8"><circle cx="4" cy="4" r="4" fill="var(--sky)"/></svg>www.clearpane-hub-services.com</div>
  <p class="abs footer-title sky" style="left:268px;top:606px">Based in North Brack<br>serving all of Edinburgh</p>
  <div class="abs contact" style="left:268px;top:632px"><svg width="8" height="10" viewBox="0 0 8 10"><path d="M4 10 C1 6 0 5 0 4 A4 4 0 0 1 8 4 C8 5 7 6 4 10 Z" fill="var(--sky)"/></svg>17 Fallowmere Close, North Brack,<br>Edinburgh EH31 4LP</div>
</section>

<!-- SIDE 2: GUTTERS -->
<section class="flyer flyer--gutters">
  <svg class="flyer-art" width="477" height="675" viewBox="0 0 477 675">
    <defs>
      <linearGradient id="g-top" x1="0" y1="0" x2="1" y2="1"><stop offset="0" stop-color="#f2f2f2"/><stop offset=".6" stop-color="#dcdcdc"/><stop offset="1" stop-color="#8a4a36"/></linearGradient>
      <linearGradient id="g-c1" x1="0" y1="0" x2="1" y2="1"><stop offset="0" stop-color="#6c7a52"/><stop offset=".5" stop-color="#2e3fa0"/><stop offset="1" stop-color="#d9d6cc"/></linearGradient>
    </defs>
    <path d="M180 0 H477 V190 H180 Z" fill="url(#g-top)" role="img" aria-label="White fascia, soffit and gutter under a roof edge"/>
    <path d="M0 300 C60 305 130 312 205 320 C130 324 60 330 0 340 Z" fill="var(--sky)"/>
    <path d="M0 122 C120 110 250 125 330 150 C400 170 450 168 477 160 V352 C400 345 300 320 200 318 C120 316 50 305 0 305 Z" fill="var(--navy)"/>
    <circle cx="381" cy="247" r="86" fill="var(--white)"/>
    <circle cx="381" cy="247" r="81" fill="url(#g-c1)" role="img" aria-label="Blue vacuum hose clearing moss from a gutter"/>
    <rect x="176" y="370" width="88" height="58" rx="6" fill="#2b2b2b" role="img" aria-label="Handheld inspection camera monitor showing a house"/>
    <rect x="183" y="376" width="74" height="46" rx="2" fill="#5e8fb8"/>
    <path d="M0 577 C150 566 330 559 477 560 V600 H0 Z" fill="var(--sky)"/>
    <path d="M0 590 C150 578 330 570 477 570 V675 H0 Z" fill="var(--navy)"/>
    <path d="M261 27 H345 V17 L365 40 L345 63 V53 H261 Z" fill="var(--green)"/>
    <path d="M232 77 H316 V67 L336 90 L316 113 V103 H232 Z" fill="var(--green)"/>
    <path d="M200 133 H284 V123 L304 146 L284 169 V159 H200 Z" fill="var(--green)"/>
  </svg>

  <div class="arrow-label" style="left:266px;top:25px">Gutter</div>
  <div class="arrow-label" style="left:236px;top:75px">Fascia</div>
  <div class="arrow-label" style="left:208px;top:131px">Soffit</div>

  <div class="brand"><span class="brand-mark"></span><span class="brand-name">ClearPane Hub</span></div>

  <h1>
    <span class="abs headline-line white" style="left:24px;top:164px;font-size:24px;font-weight:500;letter-spacing:1.5px">DON’T LET</span>
    <span class="abs headline-line sky" style="left:23px;top:190px;font-size:45px">BLOCKED</span>
    <span class="abs headline-line white" style="left:24px;top:234px;font-size:39px">GUTTERS</span>
  </h1>
  <p class="abs yellow" style="left:24px;top:273px;font-size:18px;font-weight:700;line-height:1">CAUSE COSTLY DAMAGE</p>

  <p class="abs small-bold wrap" style="left:25px;top:349px;width:220px">We inspect before we clean saving you time and money.</p>
  <p class="abs red" style="left:25px;top:377px;font-size:13px;font-weight:800;line-height:1">FREE GUTTER CHECK</p>
  <p class="abs wrap" style="left:25px;top:393px;width:150px;font-size:8px;line-height:1.25"><b>With LoftEye Inspection Cam</b><br>We show you what’s really going on before recommending service.</p>

  <p class="abs" style="left:25px;top:446px;font-size:11px;font-weight:800;line-height:1">WE OFFER</p>
  <svg class="abs" style="left:88px;top:450px" width="204" height="26" viewBox="0 0 204 26"><path d="M0 1 H200 Q203 1 203 4 V26" fill="none" stroke="#9a9ab0" stroke-width=".8"/></svg>
  <div class="tile" style="left:25px"><div class="tile-photo" style="background:linear-gradient(135deg,#a48a72,#6b4c3e)" role="img" aria-label="Conservatory cleaned from the ground"></div><p class="tile-caption">Safe, No-Ladder<br>Cleaning</p></div>
  <div class="tile" style="left:89px"><div class="tile-photo" style="background:linear-gradient(135deg,#7d8c6a,#4b5a40)" role="img" aria-label="Gutter being cleared of moss"></div><p class="tile-caption">Removes Moss,<br>Leaves &amp; Debris</p></div>
  <div class="tile" style="left:153px"><div class="tile-photo" style="background:linear-gradient(135deg,#b9d86b,#4e7a2a)" role="img" aria-label="Water dripping from a downpipe"></div><p class="tile-caption">Prevents Overflow,<br>Damp &amp; Water<br>Damage</p></div>
  <div class="tile" style="left:217px"><div class="tile-photo" style="background:linear-gradient(135deg,#d9c3b0,#9a8a80)" role="img" aria-label="Customer service adviser with a headset"></div><p class="tile-caption">Fast, Clean<br>&amp; Fully Insured</p></div>

  <div class="why">
    <div class="why-head">Why&nbsp;<b class="sky">Choose Us?</b></div>
    <div class="why-item" style="top:52px"><span class="why-icon"><svg width="10" height="10" viewBox="0 0 10 10"><path d="M1 5 L4 8 L9 2" fill="none" stroke="#fff" stroke-width="1.5"/></svg></span>Friendly,<br>professional service</div>
    <div class="why-item" style="top:89px"><span class="why-icon"><svg width="10" height="10" viewBox="0 0 10 10"><path d="M1 5 L4 8 L9 2" fill="none" stroke="#fff" stroke-width="1.5"/></svg></span>Reliable and<br>efficient</div>
    <div class="why-item" style="top:126px"><span class="why-icon"><svg width="10" height="10" viewBox="0 0 10 10"><path d="M1 5 L4 8 L9 2" fill="none" stroke="#fff" stroke-width="1.5"/></svg></span>Fully licensed<br>and insured</div>
    <div class="why-item" style="top:164px;border-bottom:none"><span class="why-icon"><svg width="10" height="10" viewBox="0 0 10 10"><path d="M1 5 L4 8 L9 2" fill="none" stroke="#fff" stroke-width="1.5"/></svg></span>Excellent customer<br>satisfaction</div>
  </div>

  <div class="abs" style="left:25px;top:546px;width:76px;height:19px;border-radius:4px;background:var(--yellow);font-size:10px;font-weight:600;display:flex;align-items:center;justify-content:center">Licensed by</div>
  <p class="abs" style="left:107px;top:551px;font-size:7.5px;font-weight:600;line-height:1">Borough of Marlow Council</p>
  <div class="abs" style="left:224px;top:543px;width:1px;height:25px;background:var(--navy)"></div>
  <p class="abs" style="left:230px;top:547px;font-size:7px;font-weight:600;line-height:1.25">Professional.<br>Affordable. Local.</p>

  <p class="abs footer-title sky" style="left:32px;top:600px">Stay ahead of leaks<br>book your gutter check today!</p>
  <div class="abs contact" style="left:32px;top:627px"><svg width="8" height="8" viewBox="0 0 8 8"><circle cx="4" cy="4" r="4" fill="var(--sky)"/></svg>0800 473 1926</div>
  <div class="abs contact" style="left:32px;top:641px"><svg width="8" height="8" viewBox="0 0 8 8"><circle cx="4" cy="4" r="4" fill="var(--sky)"/></svg>www.clearpane-hub-services.com</div>
  <p class="abs footer-title red" style="left:264px;top:609px;font-size:12.5px">Get free quote today!</p>
  <div class="abs contact" style="left:264px;top:628px"><svg width="8" height="10" viewBox="0 0 8 10"><path d="M4 10 C1 6 0 5 0 4 A4 4 0 0 1 8 4 C8 5 7 6 4 10 Z" fill="var(--sky)"/></svg>17 Fallowmere Close, North Brack,<br>Edinburgh EH31 4LP</div>
</section>

</main>
</body>
</html>
```